Maple n Brook - Contact/Landing Page

I need a landing page which will essentially be the page that customers will go to from the 'website' link on QTV listing. It will provide a short overview of services which need to be selectable. a little further down can capture some contact details followed by a large Submit Now button etc...

I have some icon/logo's that can be utilised at the bottom of the page as industry type references.

Target Market(s)

End of Lease Cleaning Services

Industry/Entity Type

Cleaning Service

Colors

Designer to choose colors to be used in the design.

Requirements
Must have
• As per description
Should not have
• Colours to match my website maplenbrook.com.au

```html
<!DOCTYPE html>
<html lang="en">
<head>
<meta charset="utf-8">
<title>Maple n Brook – End of Lease Services</title>
<link href="https://fonts.googleapis.com/css2?family=Mulish:ital,wght@0,400;0,500;0,600;0,700;0,800;1,800&display=swap" rel="stylesheet">
<style>
:root{
  --brand-blue:#2f86c9;
  --button-blue:#1aa0e6;
  --ink:#111111;
  --body-text:#222222;
  --muted:#8a8a8a;
  --line:#c9c9c9;
  --card-line:#e6e6e6;
  --footer-bg:#1f2631;
  --footer-bar:#1e7fc8;
  --white:#ffffff;
}
*{box-sizing:border-box;margin:0;padding:0}
html,body{width:1200px;height:2761px;overflow:hidden;background:var(--white)}
body{position:relative;font-family:'Mulish',sans-serif;color:var(--body-text)}
.abs{position:absolute}

/* hero */
.hero{left:0;top:0;width:1200px;height:634px;
  background:
    radial-gradient(ellipse 70% 60% at 50% 45%,rgba(255,255,255,.28),rgba(0,0,0,0) 70%),
    linear-gradient(90deg,rgba(40,40,45,.45) 0%,rgba(0,0,0,0) 25%,rgba(0,0,0,0) 75%,rgba(40,40,45,.35) 100%),
    linear-gradient(180deg,#6f6f72 0%,#a9a8a6 30%,#c2c0bc 55%,#7a6a58 78%,#5a4634 100%)}
.hero-brand{left:0;top:236px;width:1200px;display:flex;justify-content:center;align-items:center;gap:16px}
.hero-brand .mark{width:44px;height:44px;border-radius:50%;background:var(--brand-blue)}
.hero-brand .name{font-size:60px;font-weight:800;color:var(--brand-blue);letter-spacing:1px}
.hero-title{left:0;top:392px;width:1228px;text-align:center;font-size:41px;font-weight:800;font-style:italic;color:var(--white)}

/* services */
.service-photo{width:410px;height:270px}
.photo-mop{left:601px;top:680px;background:
  linear-gradient(180deg,rgba(0,0,0,0) 55%,rgba(150,120,90,.35) 100%),
  linear-gradient(90deg,#d6d3cc 0%,#a8cc3a 22%,#c9c4ba 40%,#e3e0da 60%,#5d7896 80%,#cfc9bf 100%)}
.photo-carpet{left:187px;top:952px;background:
  linear-gradient(180deg,#e6e2dc 0%,#cfcac3 30%,#8e8f95 55%,#6c6d74 100%)}
.photo-pest{left:602px;top:1225px;background:
  linear-gradient(90deg,#c8bfb2 0%,#b3a999 40%,#e4e2de 65%,#d7d3cd 85%,#8fa86a 100%)}
.service{width:330px}
.service .check{position:absolute;left:0;top:0;width:36px;height:34px}
.service h2{font-size:24px;font-weight:500;color:var(--ink);margin-left:59px}
.service p{font-size:17.5px;line-height:27px;color:var(--body-text);margin-left:59px;margin-top:10px}
.service.active h2{color:var(--brand-blue);font-weight:600}
.svc-property{left:187px;top:757px}
.svc-carpet{left:645px;top:1047px;width:370px}
.svc-carpet p{margin-left:61px;margin-top:6px}
.svc-pest{left:210px;top:1298px;width:370px}
.svc-pest p{margin-left:61px;margin-top:6px}

/* booking */
.booking{left:0;top:1573px;width:1200px;height:479px;
  background:linear-gradient(90deg,#dfe8ec 0%,#eef2f4 50%,#f7f9fa 75%,#eef2f4 100%)}
.booking-photo{left:0;top:1573px;width:600px;height:479px;
  background:
    linear-gradient(90deg,rgba(238,242,244,0) 70%,#eef2f4 100%),
    linear-gradient(90deg,#b9cbd0 0%,#8fae8a 10%,#4f7db6 28%,#3f6fac 50%,#e9ecee 62%,#d8dde0 78%)}
.book-title{left:601px;top:1623px;font-size:34px;font-weight:800;font-style:italic;color:var(--ink)}
.field{left:599px;width:353px;height:42px;border:1px solid var(--line);border-radius:3px;background:var(--white);display:flex;align-items:center}
.field .icon{width:36px;height:100%;display:flex;align-items:center;justify-content:center;border-right:1px solid #e2e2e2}
.field span{font-size:12px;color:var(--muted);margin-left:12px}
.submit{left:599px;top:1958px;width:113px;height:35px;background:var(--button-blue);color:var(--white);border:none;border-radius:2px;font-family:'Mulish',sans-serif;font-size:18px;font-weight:600}

/* accreditations */
.accred-title{left:0;top:2116px;width:1200px;text-align:center;font-size:32px;font-weight:800;font-style:italic;color:var(--ink)}
.badge-card{width:253px;height:139px;background:var(--white);border:1px solid var(--card-line);box-shadow:0 1px 4px rgba(0,0,0,.08);display:flex;flex-direction:column;align-items:center;justify-content:center}
.badge{border-radius:6px}
.badge-dark{width:218px;height:90px;background:#1b1b1b}
.badge-flag{width:230px;height:62px;background:linear-gradient(90deg,#2d3f8f 0%,#c8202f 60%,#3f5ea8 100%)}
.badge-navy{width:170px;height:110px;background:#1f3f94}
.badge-green{width:233px;height:70px;background:#7ab642;border-radius:0}
.badge-ring{width:200px;height:80px;background:#1c3a64;border-radius:40px}
.licence{font-size:12px;color:var(--ink);margin-top:10px}

/* footer */
.footer{left:0;top:2562px;width:1200px;height:156px;background:var(--footer-bg)}
.contact-icon{width:53px;height:53px;border-radius:50%;background:var(--button-blue);display:flex;align-items:center;justify-content:center}
.contact-text{color:var(--white);font-size:14px;line-height:21px}
.contact-text .label{font-size:14.5px}
.contact-text .detail{font-size:13px}
.footer-bar{left:0;top:2718px;width:1200px;height:43px;background:var(--footer-bar);color:#dfeaf5;font-size:13px;text-align:center;line-height:43px}
.footer-bar strong{color:var(--white);font-weight:600}
</style>
</head>
<body>

<header class="abs hero" role="img" aria-label="Photo of a bright furnished living room with wooden floor"></header>
<div class="abs hero-brand"><span class="mark"></span><span class="name">Maple n Brook</span></div>
<h1 class="abs hero-title">End of Lease Services</h1>

<div class="abs service-photo photo-mop" role="img" aria-label="Photo of a person mopping a living room floor beside a bucket of cleaning products"></div>
<div class="abs service active svc-property">
  <svg class="check" viewBox="0 0 36 34"><rect x="2" y="4" width="28" height="28" fill="none" stroke="#2f86c9" stroke-width="3"/><path d="M8 17l7 7L34 3" fill="none" stroke="#2f86c9" stroke-width="5"/></svg>
  <h2>Property Cleaning</h2>
  <p>All interior Cleaning carried out to property&nbsp; Management requirements</p>
</div>

<div class="abs service-photo photo-carpet" role="img" aria-label="Photo of a carpet being steam cleaned with a vacuum wand"></div>
<div class="abs service svc-carpet">
  <svg class="check" viewBox="0 0 36 34" style="top:2px"><path d="M2 3h26M2 3v28h28V10" fill="none" stroke="#9a9a9a" stroke-width="2"/></svg>
  <h2>Carpet Cleaning</h2>
  <p>Carpet Steam Cleaning to Australian Standard as 3733:1995</p>
</div>

<div class="abs service-photo photo-pest" role="img" aria-label="Photo of a pest controller in protective gear spraying under a couch"></div>
<div class="abs service svc-pest">
  <svg class="check" viewBox="0 0 36 34" style="top:2px;left:0"><path d="M2 3h26M2 3v28h28V10" fill="none" stroke="#9a9a9a" stroke-width="2"/></svg>
  <h2>Pest Control</h2>
  <p>Mandatory Requirement&nbsp; for pets on premises</p>
</div>

<section class="abs booking" aria-label="Booking"></section>
<div class="abs booking-photo" role="img" aria-label="Photo of a smiling cleaner holding a mop and a bucket of cleaning supplies"></div>
<h2 class="abs book-title">Book Your Service</h2>
<div class="abs field" style="top:1679px"><div class="icon"><svg width="12" height="12" viewBox="0 0 12 12"><circle cx="6" cy="3.5" r="3" fill="#2f86c9"/><path d="M0 12c0-4 3-5 6-5s6 1 6 5z" fill="#2f86c9"/></svg></div><span>First Name*</span></div>
<div class="abs field" style="top:1734px"><div class="icon"><svg width="12" height="12" viewBox="0 0 12 12"><circle cx="6" cy="3.5" r="3" fill="#2f86c9"/><path d="M0 12c0-4 3-5 6-5s6 1 6 5z" fill="#2f86c9"/></svg></div><span>Last Name*</span></div>
<div class="abs field" style="top:1789px"><div class="icon"><svg width="12" height="12" viewBox="0 0 12 12"><path d="M2 1l3 3-1.5 1.5c.8 1.5 1.5 2.2 3 3L8 7l3 3-1.5 1.5C5 11 1 7 .5 2.5z" fill="#2f86c9"/></svg></div><span>Your Phone*</span></div>
<div class="abs field" style="top:1844px"><div class="icon"><svg width="13" height="10" viewBox="0 0 13 10"><rect width="13" height="10" rx="1" fill="#2f86c9"/><path d="M0 1l6.5 5L13 1" fill="none" stroke="#fff" stroke-width="1.2"/></svg></div><span>Your Email*</span></div>
<div class="abs field" style="top:1900px"><div class="icon"><svg width="14" height="18" viewBox="0 0 14 18"><path d="M7 17S1 10 1 6.5a6 6 0 0 1 12 0C13 10 7 17 7 17z" fill="none" stroke="#2f86c9" stroke-width="1.3"/><circle cx="7" cy="6.5" r="2" fill="none" stroke="#2f86c9" stroke-width="1.3"/></svg></div><span>Suburb</span></div>
<button class="abs submit">Submit</button>

<h2 class="abs accred-title">Our Accreditations</h2>
<div class="abs badge-card" style="left:189px;top:2174px"><div class="badge badge-dark"></div></div>
<div class="abs badge-card" style="left:474px;top:2174px"><div class="badge badge-flag"></div></div>
<div class="abs badge-card" style="left:759px;top:2174px"><div class="badge badge-navy"></div></div>
<div class="abs badge-card" style="left:331px;top:2352px"><div class="badge badge-green"></div></div>
<div class="abs badge-card" style="left:616px;top:2352px"><div class="badge badge-ring"></div><p class="licence">Pest Licence : 4081736</p></div>

<footer class="abs footer"></footer>
<div class="abs contact-icon" style="left:195px;top:2614px"><svg width="26" height="26" viewBox="0 0 24 24"><path d="M5 3l4 4-2 2c1 2.5 3.5 5 6 6l2-2 4 4-2.5 2.5C10 19 5 14 2.5 5.5z" fill="none" stroke="#fff" stroke-width="1.5"/></svg></div>
<div class="abs contact-text" style="left:259px;top:2619px"><div class="label">PHONE</div><div class="detail">0400 555 018</div></div>
<div class="abs contact-icon" style="left:415px;top:2614px"><svg width="22" height="28" viewBox="0 0 14 18"><path d="M7 17S1 10 1 6.5a6 6 0 0 1 12 0C13 10 7 17 7 17z" fill="none" stroke="#fff" stroke-width="1.1"/><circle cx="7" cy="6.5" r="2" fill="none" stroke="#fff" stroke-width="1.1"/></svg></div>
<div class="abs contact-text" style="left:475px;top:2609px"><div class="label" style="font-size:13px">SERVING</div><div class="detail">Parramatta, Baulkham Hills, Mount Druitt,<br>Seven Hills, Blacktown, Penrith,Hills District.</div></div>
<div class="abs contact-icon" style="left:793px;top:2614px"><svg width="26" height="24" viewBox="0 0 26 24"><path d="M2 10l11-8 11 8v12H2z" fill="none" stroke="#fff" stroke-width="1.5"/><path d="M2 10l11 7 11-7" fill="none" stroke="#fff" stroke-width="1.5"/></svg></div>
<div class="abs contact-text" style="left:856px;top:2619px"><div class="label">EMAIL</div><div class="detail">info@maplenbrook.com.au</div></div>
<div class="abs footer-bar">Copyright © 2021 <strong>Maple n Brook.</strong> All Rights Reserved.</div>

</body>
</html>
```